Verlindo Magician

I want the business card for my business to give to people who watch that later I will be employed to show magic here is my website http://www.verlindoillusions.example/I want the interesting design , i am very opened for formal and informal, I watch a lot of design so don't stick to the common shape and form but i hope it can also be produced the thing to write on will be the same as in picture that i will upload , i also will upload the logo for you that so can be easy to useDenis CostilleMagicianMAGICIAN VERLINDO 17 rue des Tilleuls - 25000 BESANÇON contact@verlindoillusions.example tel. 0381 946 157 tel. 0674 219 503

```html
<!DOCTYPE html>
<html lang="fr">
<head>
<meta charset="utf-8">
<title>Verlindo Magician – Business Card</title>
<link href="https://fonts.googleapis.com/css2?family=Poppins:wght@300;400;600&display=swap" rel="stylesheet">
<style>
  :root {
    --stage: #e6e4e0;
    --card: #ffffff;
    --ink: #111111;
    --grey: #5f5f5f;
    --rule: #4a4a4a;
    --accent: #e8231f;
    --portrait-dark: #1a1a1a;
    --portrait-light: #3a3a3a;
  }
  * { box-sizing: border-box; margin: 0; padding: 0; }
  html, body {
    width: 1200px; height: 768px; overflow: hidden;
    background: var(--stage);
    font-family: "Poppins", sans-serif;
  }
  .stage {
    width: 1200px; height: 768px;
    display: flex; justify-content: center; align-items: center; gap: 90px;
  }
  .card {
    width: 380px; height: 640px;
    background: var(--card);
    border-radius: 22px;
    box-shadow: 0 10px 30px rgba(0,0,0,.18);
    position: relative;
    display: flex; flex-direction: column; align-items: center;
  }
  .portrait {
    background: linear-gradient(180deg, var(--portrait-light), var(--portrait-dark));
    border-radius: 46% 46% 12px 12px;
  }
  /* front */
  .card--front .portrait { width: 250px; height: 270px; margin-top: 120px; }
  .card--front .name {
    margin-top: 56px;
    font-weight: 600; font-size: 34px; letter-spacing: 2px;
    color: var(--ink); text-transform: uppercase;
  }
  .card--front .role {
    margin-top: 4px;
    font-weight: 300; font-size: 15px; letter-spacing: 4px;
    color: var(--grey);
  }
  /* back */
  .card--back .portrait { width: 180px; height: 190px; margin-top: 78px; }
  .card--back .brand {
    margin-top: 8px;
    font-weight: 300; font-size: 40px; letter-spacing: 2px;
    color: var(--ink);
  }
  .card--back .role {
    font-weight: 300; font-size: 11px; letter-spacing: 3px;
    color: var(--grey); margin-top: -2px;
  }
  .icon-row {
    margin-top: 26px; width: 300px;
    display: flex; align-items: center; gap: 6px;
  }
  .icon-row .rule { flex: 1; height: 1px; background: var(--rule); }
  .icon-row svg { width: 24px; height: 24px; display: block; }
  .contact {
    margin-top: 20px; text-align: center;
    font-weight: 400; font-size: 12.5px; line-height: 1.55;
    color: var(--grey); letter-spacing: .5px;
  }
  .contact .block + .block { margin-top: 10px; }
</style>
</head>
<body>
<main class="stage">

  <section class="card card--front">
    <div class="portrait" role="img" aria-label="Black and white illustrated portrait of the magician holding a playing card"></div>
    <h1 class="name">Marc Ravoulet</h1>
    <p class="role">MAGICIEN</p>
  </section>

  <section class="card card--back">
    <div class="portrait" role="img" aria-label="Black and white illustrated portrait of the magician holding a playing card"></div>
    <p class="brand">VERLINDO</p>
    <p class="role">MAGICIEN</p>

    <div class="icon-row">
      <span class="rule"></span>
      <svg viewBox="0 0 24 24" aria-label="Address">
        <circle cx="12" cy="12" r="12" fill="#111"/>
        <circle cx="12" cy="12" r="9" fill="var(--accent)"/>
        <path d="M12 6.5a3.5 3.5 0 0 0-3.5 3.5c0 2.6 3.5 6.5 3.5 6.5s3.5-3.9 3.5-6.5A3.5 3.5 0 0 0 12 6.5z" fill="#111"/>
        <circle cx="12" cy="10" r="1.3" fill="var(--accent)"/>
      </svg>
      <svg viewBox="0 0 24 24" aria-label="Phone">
        <circle cx="12" cy="12" r="12" fill="#111"/>
        <circle cx="12" cy="12" r="9" fill="var(--accent)"/>
        <path d="M8.5 7l2 2-1 1.3a6 6 0 0 0 3.2 3.2L14 12.5l2 2-1.2 1.6c-3.6-.3-6.6-3.3-6.9-6.9z" fill="#111"/>
      </svg>
      <svg viewBox="0 0 24 24" aria-label="Email">
        <circle cx="12" cy="12" r="12" fill="#111"/>
        <circle cx="12" cy="12" r="9" fill="var(--accent)"/>
        <rect x="7" y="8.5" width="10" height="7" fill="#111"/>
        <path d="M7.3 9l4.7 3.5L16.7 9" fill="none" stroke="var(--accent)" stroke-width="1"/>
      </svg>
      <svg viewBox="0 0 24 24" aria-label="Website">
        <circle cx="12" cy="12" r="12" fill="#111"/>
        <circle cx="12" cy="12" r="9" fill="var(--accent)"/>
        <circle cx="12" cy="12" r="5" fill="none" stroke="#111" stroke-width="1.3"/>
        <ellipse cx="12" cy="12" rx="2" ry="5" fill="none" stroke="#111" stroke-width="1.1"/>
        <line x1="7" y1="12" x2="17" y2="12" stroke="#111" stroke-width="1.1"/>
      </svg>
      <span class="rule"></span>
    </div>

    <div class="contact">
      <div class="block">
        <p>MAGICIAN VERLINDO</p>
        <p>17 rue des Tilleuls - 25000 BESANÇON</p>
      </div>
      <div class="block">
        <p>0381 946 157 | 0674 219 503</p>
        <p>contact@verlindoillusions.example</p>
        <p>www.verlindoillusions.example</p>
      </div>
    </div>
  </section>

</main>
</body>
</html>
```